Wedding filmmaker needs artistic business card design - brightwaterreels.ca

We are high end wedding filmmakers in a major market who produce cinematic wedding films. We require a business card design that communicates our quality, artistry, and professionalism yet looks progressive and friendly. Colors and design should skew appeal more to the bride-to-be who is usually the decision maker but not be overtly feminine per se. This means generally light pastel shades of ivory, purple, pink, yellow, as examples.
We already have a name logo established: the words "Brightwater Reels" in the font Great Vibes. Designs must use Kraft natural cardstock as the print stock and am leaning heavily toward our name logo in white, but I am open to black as well. Please design any color elements with spot white underneath where possible.
Do not try to compliment or take inspiration from our website design. Treat the card design as a separate stand alone.
Thank you so much for your hard work!

Target Market(s)

Affluent couples spending $50,000+ on their wedding

Industry/Entity Type

Progressive

Contact Information for Business Card

Peter Brightwater
Producer
905-482-7139
www.brightwaterreels.ca
peter@brightwaterreels.ca
chirpline @brightwater287

Font styles to use
Serif
Sans Serif

Requirements
Must have
• - Brightwater Reels name logo (reference GIF uploaded for reference only) and catch phrase: Breathtaking wedding films (I'm open to capitalizing all three words, or just first, or all in small caps). I favor logo, and catch phrase on front of card and my contact details on the other side but if you feel strongly about a different design, go for it!
• - Design must be submitted shown on Kraft natural cardstock NOT WHITE cardstock, If you're not familiar with Kraft, this is what it looks like: http://www.quillandlatchjournal.com/wp-content/uploads/2013/07/il_570xN.382745196_kq3m.jpg
Nice to have
• - An original graphic element (eg. movie reel, bouquet, confetti, etc.) that compliments the name logo but is subtle and discreet, doesn't overpower or entangle it.
• -Great use of balance, composition, negative space, etc. I like clean tasteful design
Should not have
• -Lousy boring clip art.
• -Graphic elements, fonts, or color palette from our website
• -White cardstock background
• -designs you have previously submitted for other contests
• -Bold dark colors (eg. red, orange navy blue, etc.)
• -High tech futuristic designs like you'd create for a software company

```html
<!DOCTYPE html>
<html lang="en">
<head>
<meta charset="utf-8">
<title>Brightwater Reels – Business Card</title>
<link href="https://fonts.googleapis.com/css2?family=Open+Sans:wght@300;400;600&display=swap" rel="stylesheet">
<style>
  :root{
    --bg:#efebe4;
    --kraft:#b98d5e;
    --kraft-deep:#a97d4f;
    --lavender:#c6b6da;
    --lavender-soft:#d9cde6;
    --blush:#eec9cf;
    --ivory:#f8f2e4;
    --white:#ffffff;
    --ink:#4a3526;
    --ink-soft:#7a6250;
  }
  *{box-sizing:border-box;margin:0;padding:0}
  html,body{width:1200px;height:901px;overflow:hidden;background:var(--bg)}
  body{position:relative;font-family:"Open Sans",Arial,sans-serif}

  .card{position:absolute;width:560px;height:320px;overflow:hidden;
        box-shadow:0 6px 18px rgba(60,40,20,.18);background:var(--kraft)}
  .card--front{left:320px;top:95px}
  .card--back{left:320px;top:485px}

  /* front */
  .band{position:absolute;left:0;width:100%}
  .band--top{top:0;height:108px;background:var(--lavender)}
  .band--line-top{top:108px;height:6px;background:var(--ivory)}
  .band--middle{top:114px;height:114px;background:var(--kraft)}
  .band--line-bottom{top:228px;height:6px;background:var(--ivory)}
  .band--bottom{top:234px;height:86px;background:var(--lavender)}
  .brand{position:absolute;left:0;right:0;top:128px;text-align:center}
  .brand__name{font-weight:300;font-size:46px;color:var(--white);letter-spacing:.5px;line-height:1.1}
  .brand__tagline{font-size:15px;color:var(--ivory);margin-top:4px;padding-left:120px}

  /* back */
  .back__brand{position:absolute;right:70px;top:30px;text-align:right}
  .back__brand .brand__name{font-size:40px}
  .back__brand .brand__tagline{padding-left:0;font-size:13px;margin-top:4px}
  .tab{position:absolute}
  .tab--right{right:0;top:120px;width:60px;height:26px;border-radius:12px 0 0 0;background:var(--lavender)}
  .rule{position:absolute;left:0;width:100%;height:5px;background:var(--lavender)}
  .rule--top{top:146px}
  .rule--bottom{top:262px}
  .contact-band{position:absolute;left:0;top:151px;width:100%;height:111px;background:var(--ivory);color:var(--ink)}
  .person{position:absolute;left:34px;top:18px}
  .person__name{font-size:26px;font-weight:400;line-height:1.1}
  .person__role{font-size:13px;color:var(--ink-soft);margin-top:2px}
  .divider{position:absolute;left:262px;top:18px;width:1px;height:74px;background:var(--kraft)}
  .contacts{position:absolute;left:286px;top:12px;list-style:none;font-size:13.5px;line-height:22px}
  .contacts li{display:flex;align-items:center;gap:10px}
  .contacts svg{width:13px;height:13px;flex:none}
  .tab--left{left:0;top:267px;width:120px;height:16px;border-radius:0 8px 8px 0;background:var(--blush)}
</style>
</head>
<body>

<section class="card card--front" aria-label="Card front">
  <div class="band band--top"></div>
  <div class="band band--line-top"></div>
  <div class="band band--middle"></div>
  <div class="band band--line-bottom"></div>
  <div class="band band--bottom"></div>
  <div class="brand">
    <p class="brand__name">Brightwater Reels</p>
    <p class="brand__tagline">Breathtaking Wedding Films</p>
  </div>
</section>

<section class="card card--back" aria-label="Card back">
  <div class="back__brand">
    <p class="brand__name">Brightwater Reels</p>
    <p class="brand__tagline">Breathtaking Wedding Films</p>
  </div>
  <div class="tab tab--right"></div>
  <div class="rule rule--top"></div>
  <div class="contact-band">
    <div class="person">
      <p class="person__name">Peter</p>
      <p class="person__role">Brightwater &nbsp;Producer</p>
    </div>
    <div class="divider"></div>
    <ul class="contacts">
      <li><svg viewBox="0 0 16 16"><path fill="#4a3526" d="M3.5 1.5l2.5 0 1 3.5-1.6 1.2c.8 1.8 2.2 3.2 4 4l1.2-1.6 3.5 1v2.5c0 .8-.7 1.4-1.5 1.4C6.6 13.3 2.7 9.4 2.1 3c0-.8.6-1.5 1.4-1.5z"/></svg>905-482-7139</li>
      <li><svg viewBox="0 0 16 16"><circle cx="8" cy="8" r="6" fill="#4a3526"/></svg>chirpline @brightwater287</li>
      <li><svg viewBox="0 0 16 16" fill="none" stroke="#4a3526" stroke-width="1.4"><circle cx="8" cy="8" r="6.5"/><ellipse cx="8" cy="8" rx="3" ry="6.5"/><path d="M1.5 8h13"/></svg>www.brightwaterreels.ca</li>
      <li><svg viewBox="0 0 16 16" fill="none" stroke="#4a3526" stroke-width="1.4"><rect x="1.5" y="3.5" width="13" height="9"/><path d="M1.5 3.5l6.5 5 6.5-5"/></svg>peter@brightwaterreels.ca</li>
    </ul>
  </div>
  <div class="rule rule--bottom"></div>
  <div class="tab tab--left"></div>
</section>

</body>
</html>
```